Computer consultant business card

Bexil Software is a newly started computer consulting company. It's a small one-man company that provides mostly Vornix applications but also websites in collaboration with designers. I'm running this company on the side of full time university studies.

I want the final design to be clean and memorable. Be creative! :)

Some inspiration:
http://www.pixelmarta.com/design/48317
http://www.pixelmarta.com/design/2739164/business-card-design-by-frostlynk
http://www.pixelmarta.com/design/604281/business-card-design-by-koralind-vestrabanu

See attachment for my company logo.
Updates

I would like to thank everyone for submitting! I'll need a couple of days to review and ultimately select a design.

Target Market(s)

Non-technical entrepreneurs and small companies.

Industry/Entity Type

University

Requirements
Must have
• My company logo.
In any way, both colors from my logo.
First- and last name, e-mail and phone number.
Double-sided design.
Nice to have
• Something creative with the symbol in my logo

```html
<!DOCTYPE html>
<html lang="en">
<head>
<meta charset="utf-8">
<title>Bexil Software – Business Card</title>
<link rel="stylesheet" href="https://fonts.googleapis.com/css2?family=Hind:wght@400;500;600&family=Quicksand:wght@600&display=swap">
<style>
  :root {
    --stage: #e9e6e1;
    --ink: #2f2d2f;
    --blue: #4472c1;
    --white: #ffffff;
    --black: #050505;
    --slate: #3a3d48;
    --slate-blue: #4a5a80;
    --label: #1e1e1e;
  }
  * { margin: 0; padding: 0; box-sizing: border-box; }
  html, body { width: 1200px; height: 788px; overflow: hidden; }
  body {
    background: var(--stage);
    font-family: "Hind", Arial, sans-serif;
    position: relative;
  }
  .side-label {
    position: absolute;
    width: 526px;
    text-align: center;
    font-size: 21px;
    color: var(--label);
    font-weight: 400;
  }
  .card {
    position: absolute;
    width: 526px;
    height: 300px;
    border-radius: 22px;
    overflow: hidden;
    box-shadow: 0 3px 8px rgba(0,0,0,.25);
  }
  .card--front { left: 56px; top: 74px; background: var(--white); }
  .card--back-light { left: 622px; top: 74px; background: var(--white); }
  .card--back-dark { left: 53px; top: 445px; background: var(--black); }
  .card--back-slate {
    left: 622px; top: 445px;
    background: radial-gradient(ellipse 90% 85% at 60% 95%, var(--slate-blue), var(--slate) 75%);
  }
  .wave { position: absolute; left: 0; top: 0; width: 526px; height: 130px; }
  .holder {
    position: absolute; right: 30px; top: 26px;
    text-align: right; color: var(--white);
  }
  .holder__name { font-size: 18px; font-weight: 600; line-height: 1.2; }
  .holder__role { font-size: 13px; line-height: 1.4; }
  .brand {
    position: absolute;
    display: flex; align-items: center;
    font-family: "Quicksand", "Hind", sans-serif;
    font-weight: 600;
    letter-spacing: 1px;
  }
  .brand__dot { border-radius: 50%; background: var(--blue); flex: none; }
  .brand--front { left: 44px; top: 128px; gap: 18px; font-size: 60px; color: var(--ink); }
  .brand--front .brand__dot { width: 76px; height: 76px; }
  .brand--back { left: 50%; top: 88px; transform: translateX(-50%); gap: 24px; font-size: 76px; }
  .brand--back .brand__dot { width: 104px; height: 104px; }
  .brand--ink { color: var(--ink); }
  .brand--light { color: var(--white); }
  .contact {
    position: absolute; right: 30px; bottom: 20px;
    text-align: right; font-size: 13.5px; color: var(--ink); line-height: 1.35;
  }
  .contact b { font-style: italic; font-weight: 600; }
  .web {
    position: absolute; left: 0; right: 0; bottom: 32px;
    text-align: center; font-size: 18px; letter-spacing: 3.2px;
  }
  .web--ink { color: var(--ink); }
  .web--light { color: var(--white); }
  .texture {
    position: absolute;
    border-radius: 50%;
  }
  .texture--top {
    left: 40px; top: -60px; width: 220px; height: 170px;
    background: radial-gradient(closest-side, rgba(90,90,95,.55), rgba(0,0,0,0));
  }
  .texture--bottom {
    left: 330px; top: 170px; width: 240px; height: 170px;
    background: radial-gradient(closest-side, rgba(120,110,120,.55), rgba(0,0,0,0));
  }
</style>
</head>
<body>
  <div class="side-label" style="left:56px;top:33px;">Front</div>
  <div class="side-label" style="left:622px;top:33px;">Back - 1</div>
  <div class="side-label" style="left:53px;top:404px;">Back - 2</div>
  <div class="side-label" style="left:622px;top:404px;">Back - 3</div>

  <section class="card card--front">
    <svg class="wave" viewBox="0 0 526 130" aria-hidden="true">
      <path d="M0 0 H526 V70 C440 100 330 112 220 88 C140 70 70 45 0 52 Z" fill="var(--ink)"/>
      <path d="M0 52 C70 45 140 70 220 88 C330 112 440 100 526 70 V80 C440 112 330 122 220 98 C140 80 70 58 0 64 Z" fill="var(--white)"/>
      <path d="M0 64 C70 58 140 80 220 98 C330 122 440 112 526 80 V90 C440 124 330 134 220 110 C140 92 70 72 0 80 Z" fill="var(--blue)"/>
    </svg>
    <div class="holder">
      <div class="holder__name">First Name Last Name</div>
      <div class="holder__role">Designation</div>
    </div>
    <div class="brand brand--front"><span class="brand__dot"></span><span>bexil</span></div>
    <div class="contact">
      <div><b>p</b> : +12 345 6789</div>
      <div><b>e</b> : info@website.com</div>
    </div>
  </section>

  <section class="card card--back-light">
    <div class="brand brand--back brand--ink"><span class="brand__dot"></span><span>bexil</span></div>
    <div class="web web--ink">www.website.com</div>
  </section>

  <section class="card card--back-dark">
    <div class="texture texture--top" role="img" aria-label="Perforated metal dot texture"></div>
    <div class="texture texture--bottom" role="img" aria-label="Perforated metal dot texture"></div>
    <div class="brand brand--back brand--light"><span class="brand__dot"></span><span>bexil</span></div>
    <div class="web web--light">www.website.com</div>
  </section>

  <section class="card card--back-slate">
    <div class="brand brand--back brand--light"><span class="brand__dot"></span><span>bexil</span></div>
    <div class="web web--light">www.website.com</div>
  </section>
</body>
</html>
```